Commercial, Public Works, Contractor needs a modern web design

We are a General and Engineering contracting firm with vast experience in our industry. Our focus is on Commercial, Tenant Improvement, Restaurants, and Public Works. We are opening a new business and would like that excitement and energy to show through the new web design. The colors we like are black, red and grey, we are open to color ideas. Attached is our logo design.

Industry/Entity Type

Restaurant

```html
<!DOCTYPE html>
<html lang="en">
<head>
<meta charset="utf-8">
<title>Ridgeline Builders, Inc. — General Contractor and Engineer</title>
<link href="https://fonts.googleapis.com/css2?family=Open+Sans:wght@400;600;700&family=Raleway:wght@300;800&family=Arimo:wght@400;700&family=Great+Vibes&display=swap" rel="stylesheet">
<style>
  :root {
    --red: #c1091a;
    --red-dark: #a30715;
    --black: #111111;
    --nav: #151515;
    --ink: #2a2a2a;
    --text: #6e6e6e;
    --line: #dcdcdc;
    --panel: #f3f3f3;
    --white: #ffffff;
  }
  * { box-sizing: border-box; margin: 0; padding: 0; }
  html, body { width: 720px; height: 1200px; overflow: hidden; background: var(--white); }
  body { position: relative; font-family: "Arimo", Arial, sans-serif; color: var(--text); }
  .abs { position: absolute; }

  .top-rule { left: 0; top: 0; width: 720px; height: 2px; background: var(--red); }

  /* header */
  .brand { left: 85px; top: 30px; display: flex; align-items: center; gap: 7px; }
  .brand-mark { width: 22px; height: 22px; border-radius: 50%; background: var(--red); }
  .brand-name { font-family: "Open Sans", sans-serif; font-weight: 700; font-size: 15px; color: var(--red); letter-spacing: .2px; }
  .call { left: 516px; top: 32px; display: flex; align-items: center; gap: 7px; font-family: "Open Sans", sans-serif; font-weight: 700; font-size: 9px; color: #333; }
  .call-icon { width: 20px; height: 20px; border: 1.5px solid var(--red); border-radius: 50%; display: flex; align-items: center; justify-content: center; }

  /* nav */
  .nav { left: 0; top: 84px; width: 720px; height: 33px; background: linear-gradient(#1f1f1f, #0c0c0c); }
  .nav-item { top: 0; height: 33px; line-height: 33px; font-family: "Open Sans", sans-serif; font-size: 8.5px; color: #eee; }
  .nav-item.active { left: 85px; width: 59px; text-align: center; background: var(--red); }
  .search { left: 504px; top: 8px; width: 120px; height: 17px; background: #0a0a0a; font-size: 7px; color: #ccc; line-height: 17px; padding-left: 12px; }
  .search svg { position: absolute; right: 10px; top: 3px; }

  /* hero */
  .hero { left: 0; top: 117px; width: 720px; height: 313px; background: linear-gradient(100deg, #8a8f95 0%, #a9a394 35%, #6d7f94 62%, #3f6b9c 80%, #c9ae66 100%); }
  .hero-title { left: 49px; top: 114px; color: var(--white); font-family: "Raleway", sans-serif; text-shadow: 0 1px 3px rgba(0,0,0,.35); }
  .hero-title .light { display: block; font-weight: 300; font-size: 25px; letter-spacing: .5px; }
  .hero-title .bold { display: block; font-weight: 800; font-size: 24px; margin-top: 4px; letter-spacing: .3px; }
  .hero-arrow { top: 206px; width: 24px; height: 23px; background: rgba(20,20,20,.75); display: flex; align-items: center; justify-content: center; }

  /* section headings */
  .heading { font-family: "Open Sans", sans-serif; font-weight: 700; font-size: 14px; color: var(--ink); text-transform: uppercase; letter-spacing: -.2px; }
  .heading em { font-style: normal; color: var(--red); }
  .rule { height: 1px; background: var(--line); }
  .rule-accent { height: 2px; }

  .copy { font-size: 7.2px; line-height: 13.6px; color: var(--text); text-align: justify; }

  .photo { background: linear-gradient(135deg, #7fa3c6, #d9d9d9); }

  /* services */
  .service { left: 452px; width: 183px; height: 25px; border: 1px solid #d6d6d6; background: linear-gradient(#fff, #f1f1f1); font-size: 8.5px; color: #444; padding-left: 18px; line-height: 23px; }
  .service .plus { position: absolute; right: 14px; top: 6px; width: 11px; height: 11px; border-radius: 50%; background: var(--red); color: #fff; font-size: 10px; line-height: 11px; text-align: center; font-weight: 700; }

  /* testimonial */
  .testimonial { left: 85px; top: 866px; width: 266px; height: 100px; background: var(--panel); border: 1px solid #e6e6e6; }
  .avatar { left: 32px; top: 15px; width: 68px; height: 68px; border-radius: 50%; border: 2px solid #fff; box-shadow: 0 0 0 1px #ccc; background: linear-gradient(#d8d8d8, #3b3b3b); }
  .quote-tail { left: 30px; top: 99px; }
  .signature { left: 110px; top: 978px; font-family: "Great Vibes", cursive; font-size: 13px; color: var(--red); }
  .signature span { color: #333; }

  .news-title { font-size: 7.2px; font-style: italic; color: var(--red); }
  .news-copy { font-size: 7.2px; line-height: 13.6px; color: var(--text); }

  /* footer */
  .footer { left: 0; top: 1020px; width: 720px; height: 136px; background: var(--red); }
  .foot-heading { font-family: "Open Sans", sans-serif; font-weight: 600; font-size: 12px; color: #fff; top: 22px; }
  .foot-rule { top: 42px; height: 1px; background: rgba(255,255,255,.75); }
  .foot-list { left: 84px; top: 55px; list-style: none; }
  .foot-list li { font-size: 7.2px; color: #fff; height: 12px; line-height: 12px; padding-left: 15px; position: relative; }
  .foot-list li::before { content: ""; position: absolute; left: 0; top: 3px; border-left: 4px solid #fff; border-top: 3px solid transparent; border-bottom: 3px solid transparent; }
  .foot-text { font-size: 7.2px; line-height: 12px; color: #fff; }
  .signup-input { left: 282px; top: 88px; width: 119px; height: 17px; background: #eee; border: 1px solid #ccc; font-size: 7px; color: #999; line-height: 15px; padding-left: 8px; }
  .signup-btn { left: 401px; top: 88px; width: 37px; height: 17px; background: var(--red-dark); color: #fff; font-size: 7px; font-weight: 700; text-align: center; line-height: 17px; }
  .contact-row { left: 483px; display: flex; align-items: center; gap: 18px; font-size: 7.2px; color: #fff; }
  .contact-row svg { width: 13px; }

  .bottom-bar { left: 0; top: 1156px; width: 720px; height: 44px; background: var(--black); }
  .copyright { left: 77px; top: 17px; font-size: 7px; color: #ddd; }
  .social { top: 12px; width: 20px; height: 20px; border-radius: 50%; border: 1px solid #bbb; }
</style>
</head>
<body>
  <div class="abs top-rule"></div>

  <header>
    <div class="abs brand">
      <span class="brand-mark"></span>
      <span class="brand-name">RIDGELINE BUILDERS, INC.</span>
    </div>
    <div class="abs call">
      <span class="call-icon">
        <svg width="10" height="10" viewBox="0 0 24 24"><path fill="#c1091a" d="M6.6 10.8a15.1 15.1 0 0 0 6.6 6.6l2.2-2.2c.3-.3.7-.4 1-.2 1.1.4 2.3.6 3.6.6.6 0 1 .4 1 1V20c0 .6-.4 1-1 1A17 17 0 0 1 3 4c0-.6.4-1 1-1h3.5c.6 0 1 .4 1 1 0 1.3.2 2.5.6 3.6.1.3 0 .7-.2 1l-2.3 2.2z"/></svg>
      </span>
      CALL US 555-204-3180
    </div>
  </header>

  <nav class="abs nav">
    <span class="abs nav-item active">HOME</span>
    <span class="abs nav-item" style="left:162px">ABOUT US</span>
    <span class="abs nav-item" style="left:238px">SERVICES</span>
    <span class="abs nav-item" style="left:309px">PROJECTS</span>
    <span class="abs nav-item" style="left:382px">CONTACT US</span>
    <div class="abs search">Search
      <svg width="11" height="11" viewBox="0 0 12 12"><circle cx="5" cy="5" r="3.6" fill="none" stroke="#ddd" stroke-width="1.3"/><line x1="7.6" y1="7.6" x2="11" y2="11" stroke="#ddd" stroke-width="1.5"/></svg>
    </div>
  </nav>

  <section class="abs hero" role="img" aria-label="Construction worker holding a yellow hard hat and rolled plans in front of a building site">
    <h1 class="abs hero-title">
      <span class="light">WE ARE AN ENGINEERING</span>
      <span class="bold">&amp; CONTRACTING COMPANY</span>
    </h1>
    <span class="abs hero-arrow" style="left:49px"><svg width="8" height="10" viewBox="0 0 8 10"><polyline points="6,1 2,5 6,9" fill="none" stroke="#fff" stroke-width="1.4"/></svg></span>
    <span class="abs hero-arrow" style="left:76px"><svg width="8" height="10" viewBox="0 0 8 10"><polyline points="2,1 6,5 2,9" fill="none" stroke="#fff" stroke-width="1.4"/></svg></span>
  </section>

  <!-- welcome -->
  <h2 class="abs heading" style="left:85px;top:450px">Welcome to <em>Ridgeline ,Inc.</em></h2>
  <div class="abs rule" style="left:85px;top:472px;width:338px"></div>
  <div class="abs rule rule-accent" style="left:85px;top:471px;width:77px;background:#bdbdbd"></div>
  <div class="abs photo" style="left:85px;top:494px;width:93px;height:72px" role="img" aria-label="Two engineers in hard hats reviewing plans before office towers"></div>
  <p class="abs copy" style="left:194px;top:488px;width:229px">Consectetuer adipiscing elit. Aenean commodo ligula eget dolor. Aenean massa. Cum sociis natoque penatibus et magnis dis parturient montes, nascetur ridiculus mus. Donec quam felis, ultricies nec, pellentesque eu, pretium quis, sem. Nulla consequat massa quis enim. Donec pede justo, fringilla vel, aliquet nec, vulputate eget, arcu. In enim justo, rhoncus ut, imperdiet a, venenatis vitae, justo.</p>
  <p class="abs copy" style="left:85px;top:580px;width:338px">Consectetuer adipiscing elit. Aenean commodo ligula eget dolor. Aenean massa. Cum sociis natoque penatibus et magnis dis parturient montes, nascetur ridiculus mus. Donec quam felis, ultricies nec, pellentesque eu, pretium quis, sem. Nulla consequat massa quis enim.</p>

  <!-- services -->
  <h2 class="abs heading" style="left:450px;top:450px">Our <em>Services</em></h2>
  <div class="abs rule" style="left:450px;top:472px;width:186px"></div>
  <div class="abs service" style="top:491px">Commercial Works<span class="plus">+</span></div>
  <div class="abs service" style="top:526px">Tenant Improvement<span class="plus">+</span></div>
  <div class="abs service" style="top:559px">Restaurants<span class="plus">+</span></div>
  <div class="abs service" style="top:593px">Public Works<span class="plus">+</span></div>

  <!-- projects -->
  <h2 class="abs heading" style="left:85px;top:647px">Recent <em>Projects</em></h2>
  <div class="abs rule" style="left:85px;top:669px;width:551px"></div>
  <svg class="abs" style="left:612px;top:649px" width="26" height="12" viewBox="0 0 26 12"><polyline points="7,1 2,6 7,11" fill="none" stroke="#ccc" stroke-width="1.5"/><polyline points="19,1 24,6 19,11" fill="none" stroke="#ccc" stroke-width="1.5"/></svg>
  <div class="abs photo" style="left:85px;top:690px;width:125px;height:104px;background:linear-gradient(135deg,#6fb0b8,#d6c9b8 60%,#8a6a5a)" role="img" aria-label="Tower crane beside a high-rise under construction"></div>
  <div class="abs photo" style="left:226px;top:690px;width:125px;height:104px;background:linear-gradient(160deg,#2d6fb8,#9cc0e4 50%,#b08a6a)" role="img" aria-label="Contractor shaking hands with clients at a building site"></div>
  <div class="abs photo" style="left:368px;top:690px;width:126px;height:104px;background:linear-gradient(150deg,#8a7a64,#2a2a2a 55%,#b7ab98)" role="img" aria-label="Workers on scaffolding at a concrete wall"></div>
  <div class="abs photo" style="left:510px;top:690px;width:125px;height:104px;background:linear-gradient(180deg,#3f72c4,#9bb5d8 40%,#b59b78)" role="img" aria-label="Row of newly built houses"></div>

  <!-- testimonials -->
  <h2 class="abs heading" style="left:85px;top:819px">Our <em>Testimonials</em></h2>
  <div class="abs rule rule-accent" style="left:85px;top:842px;width:77px;background:var(--red)"></div>
  <div class="abs testimonial">
    <div class="abs avatar" role="img" aria-label="Portrait of the client"></div>
    <p class="abs copy" style="left:94px;top:20px;width:152px">Consectetuer adipiscing elit. Aenean commodo ligula eget dolor. Aenean massa. Cum sociis natoque penatibus et magnis dis parturient montes, nascetur ridiculus mus. Donec quam felis, ultricies nec, pellentesque.</p>
  </div>
  <svg class="abs" style="left:110px;top:965px" width="14" height="8" viewBox="0 0 14 8"><polygon points="0,0 14,0 0,8" fill="#f3f3f3"/></svg>
  <div class="abs signature">Mara Lindqvist <span>(Designation)</span></div>

  <!-- news -->
  <h2 class="abs heading" style="left:372px;top:817px">Latest <em>News</em></h2>
  <div class="abs rule rule-accent" style="left:372px;top:840px;width:77px;background:var(--red)"></div>
  <div class="abs photo" style="left:374px;top:866px;width:56px;height:44px;background:linear-gradient(160deg,#7fa5cf,#6a6a6a 60%,#a08c6c)" role="img" aria-label="Steel frame structure with workers"></div>
  <p class="abs news-title" style="left:442px;top:864px">Consectetuer adipiscing elit.</p>
  <p class="abs news-copy" style="left:442px;top:876px;width:194px">&nbsp;Aenean commodo ligula eget dolor. Aenean massa. Cum sociis natoque penatibus et magnis dis parturient montes</p>
  <div class="abs photo" style="left:374px;top:923px;width:56px;height:45px;background:linear-gradient(150deg,#3c3c3c,#c45a3a 50%,#b9b0a2)" role="img" aria-label="Worker in safety gear on site"></div>
  <p class="abs news-title" style="left:442px;top:922px;font-style:normal">Consectetuer adipiscing elit.</p>
  <p class="abs news-copy" style="left:442px;top:934px;width:194px">&nbsp;Aenean commodo ligula eget dolor. Aenean massa. Cum sociis natoque penatibus et magnis dis parturient montes</p>

  <!-- footer -->
  <footer class="abs footer">
    <h3 class="abs foot-heading" style="left:83px">COMPANY</h3>
    <div class="abs foot-rule" style="left:83px;width:163px"></div>
    <ul class="abs foot-list">
      <li>Home</li><li>About us</li><li>Services</li><li>Portfolio</li><li>Contact us</li>
    </ul>

    <h3 class="abs foot-heading" style="left:281px">NEWSLETTER SIGNUP</h3>
    <div class="abs foot-rule" style="left:275px;width:163px"></div>
    <p class="abs foot-text" style="left:281px;top:52px;width:160px">Cras volutpat, ante ac gravida iaculis, dui lacus iaculis nibh, eu scelerisque.</p>
    <div class="abs signup-input">Your Email Address</div>
    <div class="abs signup-btn">Submit</div>

    <h3 class="abs foot-heading" style="left:481px">CONTACT US</h3>
    <div class="abs foot-rule" style="left:481px;width:164px"></div>
    <div class="abs contact-row" style="top:58px">
      <svg viewBox="0 0 14 12" height="11"><path d="M7 0 0 6h2v6h4V8h2v4h4V6h2z" fill="#fff"/></svg>1234 Street Name, City, Country
    </div>
    <div class="abs contact-row" style="top:79px">
      <svg viewBox="0 0 14 12" height="11"><path d="M1 3c0-2 12-2 12 0v2h-3V4H4v1H1zm2 3h8l1 5H2z" fill="#fff"/></svg>+014 555 204 318
    </div>
    <div class="abs contact-row" style="top:99px">
      <svg viewBox="0 0 14 10" height="9"><rect x="0" y="0" width="14" height="10" fill="#fff"/><polyline points="0,0 7,6 14,0" fill="none" stroke="#c1091a" stroke-width="1.2"/></svg>info@ridgelinebuild.com
    </div>
  </footer>

  <div class="abs bottom-bar">
    <p class="abs copyright">Copyright © 2014 Ridgeline Builders Inc. &nbsp;|&nbsp; All rights Reserved</p>
    <span class="abs social" style="left:528px" aria-label="Social profile"></span>
    <span class="abs social" style="left:554px" aria-label="Social profile"></span>
    <span class="abs social" style="left:580px" aria-label="Social profile"></span>
    <span class="abs social" style="left:605px" aria-label="Social profile"></span>
  </div>
</body>
</html>
```